BRIVAN 2026 Flyer for Conference

BRIVAN needs a design for a 1-page flyer that we will hand out at an upcoming event & then later post online as a pdf. There are 3 elements which need to be on the flyer:

1) A logo. This should be prominent on the design (e.g., in the middle). The flyer should use the colors that are in that logo (e.g., for accents, design elements, and/or text; not all of these have to be used):
Dark blue: #185577
Med blue: #327C9A
Teal: #4EB1C2
Light Teal: #9EDBE6

2) The conference theme -- Oceans of Knowledge: Diving into Information Literacy -- should be at the flyer's top.

3) Finally, these six tracks should be listed below the theme and the logo (it's font size should be at least a couple sizes smaller than the size used for the theme):
- Pearls of Pedagogy: Teaching Techniques that Work
- The Depth Gauge: Measuring Instructional Impact
- Techtonic Shifts: Innovation and Educational Technology
- Captain's Log: Navigating Leadership in Library Instruction
- Swimming Together: Collaborating with Others
- The Bermuda Triangle: Exploring (Seemingly) Eternal Challenges

Font styles to use
Sans Serif

Colors
0094D4
00A9DD
6FCCEA
C7EBF8
E9F6FB

Requirements
Must have
• The 3 elements listed in the description: 1) the logo, 2) the text of the theme and 3) the text for the tracks.

```html
<!DOCTYPE html>
<html lang="en">
<head>
<meta charset="utf-8">
<title>BRIVAN 2026 – Oceans of Knowledge</title>
<link rel="stylesheet" href="https://fonts.googleapis.com/css2?family=Poppins:wght@300;700;800&display=swap">
<style>
  :root {
    --dark-blue: #185577;
    --med-blue: #327C9A;
    --headline-blue: #3b93ad;
    --teal: #4EB1C2;
    --light-teal: #9EDBE6;
    --ice: #E9F6FB;
    --pale: #C7EBF8;
    --ink: #1e1e1e;
    --paper: #ffffff;
  }
  * { margin: 0; padding: 0; box-sizing: border-box; }
  html, body { width: 927px; height: 1200px; overflow: hidden; background: var(--paper); }
  .flyer {
    position: relative;
    width: 927px;
    height: 1200px;
    overflow: hidden;
    background: linear-gradient(180deg, #f4fafd 0%, var(--paper) 30%, var(--paper) 100%);
    font-family: "Poppins", sans-serif;
  }
  .mist {
    position: absolute;
    border-radius: 50%;
    filter: blur(18px);
    opacity: .55;
  }
  .mist--left { left: -60px; top: 40px; width: 360px; height: 160px; background: var(--pale); transform: rotate(-18deg); }
  .mist--right { right: -70px; top: 20px; width: 380px; height: 150px; background: var(--ice); transform: rotate(12deg); }

  .brand {
    position: absolute;
    left: 0; right: 0; top: 80px;
    text-align: center;
    color: var(--dark-blue);
  }
  .brand__name {
    display: inline-flex;
    align-items: center;
    gap: 14px;
    font-weight: 800;
    font-size: 66px;
    line-height: 1;
    letter-spacing: 1px;
  }
  .brand__dot { width: 26px; height: 26px; border-radius: 50%; background: var(--teal); }
  .brand__meta {
    margin-top: 14px;
    font-weight: 700;
    font-size: 15px;
    letter-spacing: 3px;
    color: var(--teal);
  }

  .theme {
    position: absolute;
    left: 0; right: 0; top: 268px;
    text-align: center;
    font-weight: 800;
    font-size: 60px;
    line-height: 73px;
    letter-spacing: -1px;
    text-shadow: 2px 2px 0 rgba(255,255,255,.9), 0 3px 6px rgba(24,85,119,.18);
  }
  .theme__line { display: block; }
  .theme__line--dark { color: var(--dark-blue); }
  .theme__line--mid { color: var(--headline-blue); }

  .wave-photo {
    position: absolute;
    left: 0; top: 500px;
    width: 520px; height: 700px;
    background: linear-gradient(180deg, #e3eff4 0%, #3f88a3 25%, #1b6f93 60%, #0f4a6c 100%);
  }

  .tracks {
    position: absolute;
    left: 536px; top: 523px;
    width: 380px;
    list-style: none;
  }
  .track {
    position: relative;
    padding-left: 31px;
    margin-bottom: 24px;
    line-height: 34px;
    font-size: 18.5px;
    color: var(--ink);
  }
  .track::before {
    content: "";
    position: absolute;
    left: 0; top: 11px;
    width: 13px; height: 13px;
    border-radius: 50%;
    background: var(--teal);
  }
  .track__title { display: block; font-weight: 700; }
  .track__desc { display: block; font-weight: 300; }

  .code {
    position: absolute;
    right: 22px; bottom: 16px;
    font-size: 14px;
    color: var(--ink);
  }
</style>
</head>
<body>
<main class="flyer">
  <div class="mist mist--left" aria-hidden="true"></div>
  <div class="mist mist--right" aria-hidden="true"></div>

  <header class="brand">
    <div class="brand__name"><span class="brand__dot" aria-hidden="true"></span>BRIVAN 2026</div>
    <div class="brand__meta">NORFOLK, VA · MAY 7–9</div>
  </header>

  <h1 class="theme">
    <span class="theme__line theme__line--dark">OCEANS OF KNOWLEDGE</span>
    <span class="theme__line theme__line--mid">DIVING INTO INFORMATION</span>
    <span class="theme__line theme__line--dark">LITERACY</span>
  </h1>

  <div class="wave-photo" role="img" aria-label="Photograph of a large curling ocean wave with white spray at its crest"></div>

  <ul class="tracks">
    <li class="track"><span class="track__title">PEARLS OF PEDAGOGY</span><span class="track__desc">Teaching Techniques that Work</span></li>
    <li class="track"><span class="track__title">THE DEPTH GAUGE</span><span class="track__desc">Measuring Instructional Impact</span></li>
    <li class="track"><span class="track__title">TECHTONIC SHIFTS</span><span class="track__desc">Innovation and Educational Technology</span></li>
    <li class="track"><span class="track__title">CAPTAIN'S LOG</span><span class="track__desc">Navigating Leadership in Library Instruction</span></li>
    <li class="track"><span class="track__title">SWIMMING TOGETHER</span><span class="track__desc">Collaborating with Others</span></li>
    <li class="track"><span class="track__title">THE BERMUDA TRIANGLE</span><span class="track__desc">Exploring (Seemingly) Eternal Challenges</span></li>
  </ul>

  <div class="code">C9</div>
</main>
</body>
</html>
```